Mobile Repair Service on location needs a Web Design

We are starting a new mobile device repair service called Handset Haven and our website needs a design!

Hello Designers!
First, we'd like to make clear this is more than a simple web design contest, we want the designers to create an idea. We want someone who can create the whole theme of the service's we provide. We want someone that can help design our visual branding, help us communicate a sentiment. And we are willing to pay for that.

Who are we?
Our company is based in Rotterdam, the Netherlands. We provide different services for all kinds of electronic devices. The kind of services we provide are, among other things, installations of hardware and software and the repair of broken or malfunctioning devices.
We are starting a new service that offers mobile device repairs on location, be it at the home of our customers, their office, or any other place. Just give us the address and we will come to you for the repair job. This is also our main USP. We have multiple skilled engineers who drive trough the country on a daily basis and can be on location within a working day. Repair is done immediately onsite while the customer waits. At this stage we will start with the smartphone product-group within the mobile devices. In a second phase we might also add tablets.
People don't want to be without their phone for weeks because of some parts that needed to be ordered by a repair center they had to sent their phone to. We offer a fully functional mobile repair center in the form of specially customized vans. These vans have all the tools and utilities needed by our engineers to safely repair your mobile device. Your phone is being repaired directly in front of you, the next business-day, on a location you desire.

For this new service we are creating a website called Handset Haven. The website needs a story and matching design and this is where you come in. We are not looking for a simple template design we can get from any place. We need a story. We want you to create an idea, build a unique theme or vision that helps sell the product/service. This goes beyond the design of the website. We need the whole package, the design you are creating needs to have returning elements like icons, color use, images, maybe even characters etc. You name it! There needs to be a common thread in the design so we can reuse elements in, for example, the email templates, the work order or receipt we give to our customers (we may contact the winner of the contest to design these for us as well!).

The name 'Handset Haven' is chosen. Rehab (short for rehabilitate) has a bold and playful tone to it and the design needs to reflect the name. So we're looking for a somewhat playful and cheeky design. Definitely not too serious and definitely modern. We already got a logo that we love and that fit's this description (see attached design documents for the logo). It's bold, powerful and fun. Our web design needs to reflect this as well and has to fit in with our logo.
We would really like it if the design somehow incorporates elements that highlight our unique selling points (repairs on location, we come to you etc.). We would really like some form of story telling in the design. Think clumsy people breaking their phones. Teenagers in tears because they have no access to their friends. People nowadays have the need to always be 'connected'. What happens when your phone is broken or malfunctioning? We're handling tech, we are nerds and a little bit weird, but we're professionals and here to help you with your problem. The sentiment Byte Brigade tries to communicate is something we really like. We're looking for fresh idea's, anything goes!

In an overview all Unique Selling Points of the Handset haven service:
- Professional service on location. Don’t ship to us we will come to you!
- Clear pricing upfront. No hidden cost.
- Next business-day repair.
- Backed by a professional call center open 12 hours a day and open on a Saturday as well
- Backed by a professional repair center with more then 12 years of experience
- Repair is done by certified engineers
- 1 year warranty on the repair

The process:
The main function of our website will be for customers to make a repair request. A customer will visit our website and can make a repair request immediately by going through a 'request-order-flow'. In this flow he or she will need to fill in some forms and can select wich type/model/brand of mobile device he or she has and what parts need to be repaired. After a request is placed we will call the customer back (within an hour) for a short intake and to set a date/time and location. Our engineer will meet the customer at the specified location and will repair the device onsite in one of our mobile repair centers, which is a specialized van equipped with all the tools needed for device restorations.
So in short the steps are:
- Choose your device and repair job
- Place the order
- Get a callback within the hour
- Set date and location
- We will come to you.

Website functionality:
Our website is our main form of communication. So the sentiment we want to communicate needs be reflected in the design. We need a main/front page designed (preferably a long scrolling page design) containing:
1. Customers will be able to request a repair job directly on our website. So there will need to be a prominent button/link at the top of our main page that will bring the customer to this 'request-order-flow'. This is the main flow which needs to be full focus on the front page. All other items are secondary.
2. The general information of who we are and what we do, and why the customer should choose us. Preferably in short bullet-point type keywords/sentences with icons or other visual cues. See our unique selling points to get an idea of the information that will be displayed here.
3. There needs to be a section that will explain the process (see above) of a repair request step-by- step, again in brief short key sentences and with (custom) icons.
4. There needs to be a section that explains to the customer he/she can always contact us if they are not sure what the problem is with their device, and for this reason are not sure what repair request they should order.
5. We want to implement some functionality that display customer ratings or customer reviews. So there needs to be room for some kind of widget of plugin we're going to implement which shows these reviews.
6. A 'For business section' where we will explain all the options we provide for corporate clients.
7. Social media links.
8. There needs to be a menu with buttons that leads to the all sections described in the previous points.

For now, we need a design for our front page. In the second phase, when we have picked our winner, we may ask the winner to design the page(s) for our request workflow as well.

EDIT:
Finally, we have a very specific order in mind for the different segments of our website. We would like you to add some more segments that were not in our original brief as well:

1. Top header with order/request button. (should instantly make clear our main USP, we do repairs on location)
2. Our process
3. Our unique selling points / why choose us
4. The kind of repairs we do (broken screens, broken batteries, water damage, broken camera's, no sound etc.)
5. A 'meet our team' section, where we introduce some of our engineers
6. A 'contact us for any questions' section/
7. Testimonials/user reviews
8. A section where we show key performance indicators
9. 'For businesses' sections
10.'Subscribe for newsletter' field
11. Social media buttons

Industry/Entity Type

It Service

Number of Pages Required

1 page

Font styles to use
Sans Serif

Requirements
Must have
• a main/front page, design only
• custom icons/images for banners, adverts online and in print (high res)
Nice to have
• Storytelling in our design.
• Design that fits with our brand new logo.
• Elements like icons to have a flat design.
• Keep in mind that the website will need to be responsive when designing! (Ideally provide an example of the mobile design as well)
• Create a fun and trustworthy feeling.

```html
<!DOCTYPE html>
<html lang="en">
<head>
<meta charset="utf-8">
<title>Handset Haven – Mobile Repair On Location</title>
<link href="https://fonts.googleapis.com/css2?family=Raleway:wght@300;400;600;700;800&family=Open+Sans:wght@400;600;700&display=swap" rel="stylesheet">
<style>
:root{
  --orange:#f26a21;
  --orange-light:#ff8a3d;
  --orange-deep:#e4551a;
  --ink:#2b2b2b;
  --grey:#8a8a8a;
  --line:#dcdcdc;
  --dark:#1e1f22;
  --white:#ffffff;
  --soft:#f4f4f4;
}
*{box-sizing:border-box;margin:0;padding:0}
html,body{width:1200px;height:5068px;overflow:hidden}
body{font-family:'Open Sans',Arial,sans-serif;color:var(--ink);background:var(--white);position:relative}
h1,h2,h3,h4{font-family:'Raleway',Arial,sans-serif}
section,header,footer{position:absolute;left:0;width:1200px}
.section-title{text-align:center;font-family:'Raleway',sans-serif;line-height:1.05}
.section-title .light{display:block;font-weight:300;font-size:34px;color:#555}
.section-title .bold{display:block;font-weight:700;font-size:38px;color:var(--ink)}
.section-title::after{content:"";display:block;width:60px;height:3px;background:var(--orange);margin:14px auto 0}
.btn{display:inline-block;background:var(--orange);color:#fff;font-family:'Raleway',sans-serif;font-weight:700;font-size:15px;padding:12px 26px;border-radius:24px;text-decoration:none;white-space:nowrap}
.placeholder{position:absolute}

/* header / hero */
.hero{top:0;height:680px;clip-path:polygon(0 0,100% 0,100% 92%,50% 100%,0 92%);overflow:hidden}
.hero-photo{inset:0;background:linear-gradient(160deg,#5b6670 0%,#3b434b 45%,#7d7468 100%)}
.hero-shade{position:absolute;inset:0;background:rgba(20,22,26,.45)}
.nav{position:absolute;top:0;left:0;width:1200px;height:90px;display:flex;align-items:center;padding:0 36px}
.brand{display:flex;align-items:center;gap:10px;font-family:'Raleway',sans-serif;font-weight:800;font-size:20px;color:#fff;text-transform:uppercase;line-height:1;white-space:nowrap}
.brand-dot{width:30px;height:30px;border-radius:50%;background:var(--orange);flex:none}
.menu{display:flex;gap:18px;margin-left:auto;list-style:none;font-size:13px;color:#fff;font-weight:600;white-space:nowrap}
.nav .btn{margin-left:22px;font-size:13px;padding:9px 20px}
.hero-copy{position:absolute;top:280px;left:0;width:1200px;text-align:center;color:#fff}
.hero-copy h1{font-weight:300;font-size:50px;line-height:1.15}
.hero-copy h1 strong{font-weight:700;display:block}
.hero-copy p{width:760px;margin:22px auto 30px;font-size:15px;line-height:1.6;color:#eee}

/* process */
.process{top:700px;height:470px}
.process .section-title{margin-top:40px}
.steps{display:flex;justify-content:space-between;padding:0 70px;margin-top:48px}
.step{width:190px;text-align:center}
.step-art{width:130px;height:130px;margin:0 auto;border-radius:50%;background:radial-gradient(circle,#f0ece8 0%,#dcd6cf 100%)}
.step h3{color:var(--orange);font-size:17px;font-weight:600;margin:22px 0 10px;line-height:1.3}
.step p{font-size:12px;color:var(--grey);line-height:1.55}

/* why choose us */
.why{top:1200px;height:630px;background:linear-gradient(180deg,var(--orange-light) 0%,var(--orange) 45%,var(--orange-deep) 100%);clip-path:polygon(0 8%,100% 0,100% 100%,0 100%)}
.why .section-title{margin-top:90px}
.why .section-title .light,.why .section-title .bold{color:#fff}
.why .section-title::after{background:#fff}
.usps{display:flex;justify-content:space-between;padding:0 60px;margin-top:56px}
.usp{width:142px;text-align:center;color:#fff}
.usp-ring{width:104px;height:104px;margin:0 auto;border-radius:50%;background:rgba(255,255,255,.35);display:flex;align-items:center;justify-content:center}
.usp-core{width:80px;height:80px;border-radius:50%;background:#4a4e57;display:flex;align-items:center;justify-content:center}
.usp h3{font-size:14px;font-weight:700;margin:22px 0 8px;line-height:1.35}
.usp p{font-size:11px;line-height:1.5;color:#ffe3d2}

/* what we do */
.services{top:1840px;height:540px}
.services .section-title{margin-top:36px}
.cards{display:flex;gap:28px;padding:0 78px;margin-top:40px;position:relative}
.card{width:240px;background:var(--soft);box-shadow:0 2px 6px rgba(0,0,0,.08)}
.card-photo{position:relative;height:130px}
.card h3{color:var(--orange);font-size:17px;font-weight:600;text-align:center;margin:18px 0 10px}
.card p{font-size:11.5px;color:var(--grey);line-height:1.55;padding:0 18px 22px;text-align:center}
.arrow{position:absolute;top:150px;width:20px;height:40px}
.arrow.left{left:22px}.arrow.right{right:22px}

/* team */
.team{top:2392px;height:512px;background:linear-gradient(180deg,#2a2b2e,#18191b);color:#fff}
.team-head{display:flex;padding:48px 80px 0}
.team-head h2{font-size:32px;font-weight:800;line-height:1;white-space:nowrap}
.team-head .sub{font-size:14px;margin-top:10px;color:#ddd;white-space:nowrap}
.team-head .sub b{color:var(--orange)}
.team-head p{margin-left:50px;width:740px;font-size:14px;line-height:1.6;color:#ccc}
.members{display:flex;gap:24px;padding:0 80px;margin-top:40px}
.member{width:192px}
.member-photo{position:relative;height:200px}
.member h4{font-size:13px;font-weight:700;margin-top:12px;letter-spacing:.5px}
.member span{font-size:11px;color:#aaa}

/* contact */
.contact{top:2912px;height:600px}
.contact-photo{left:0;top:0;width:640px;height:600px;background:linear-gradient(135deg,#d7dde3 0%,#9aa8b5 60%,#6d7e8e 100%)}
.contact-form{position:absolute;left:730px;top:150px;width:380px}
.contact-form h2{font-weight:300;font-size:36px;line-height:1.1}
.contact-form h2 b{font-weight:700;display:block}
.field{border-bottom:1px solid var(--line);padding:14px 0 8px;font-size:14px;color:#666;margin-top:10px}
.contact-form .btn{margin-top:30px}

/* testimonials */
.testimonials{top:3512px;height:400px}
.testimonials .section-title{margin-top:30px}
.quotes{display:flex;justify-content:space-between;padding:0 80px;margin-top:46px}
.quote{width:500px;display:flex;gap:22px;align-items:flex-start}
.quote-avatar{position:relative;flex:none;width:100px;height:100px;border-radius:50%;border:4px solid var(--orange);background:#cfc8c2}
.quote-mark{font-family:'Raleway',sans-serif;font-size:70px;line-height:.8;color:var(--orange);font-weight:800}
.quote p{font-size:13px;color:var(--grey);line-height:1.6}
.quote cite{display:block;margin-top:10px;color:var(--orange);font-style:normal;font-size:13px}

/* key performance */
.kpi{top:3920px;height:440px}
.kpi-photo{inset:0;background:linear-gradient(120deg,#4e5c69 0%,#3f5062 35%,#2f3f4f 65%,#1f2b37 100%)}
.kpi .section-title{position:relative;padding-top:40px}
.kpi .section-title .light,.kpi .section-title .bold{color:#fff}
.kpi-list{position:relative;display:flex;justify-content:space-between;padding:0 110px;margin-top:40px}
.kpi-item{width:200px;text-align:center;color:#fff}
.kpi-icon{width:120px;height:120px;margin:0 auto;border-radius:50%;background:var(--orange);border:6px solid rgba(255,255,255,.5);display:flex;align-items:center;justify-content:center}
.kpi-item h3{font-size:17px;font-weight:700;margin:20px 0 8px}
.kpi-item p{font-size:11.5px;line-height:1.5;color:#e2e6ea}

/* business */
.business{top:4360px;height:240px;display:flex;align-items:center;padding:0 90px}
.business h2{font-weight:300;font-size:32px;line-height:1.15;width:240px;border-right:3px solid var(--orange);padding-right:30px}
.business h2 b{font-weight:700;display:block}
.business .biz-copy{margin-left:50px}
.business h3{color:var(--orange);font-weight:400;font-size:28px}
.business ul{margin-top:16px;padding-left:20px;color:#d9241c;font-size:15px;line-height:1.7;font-weight:600}

/* footer */
.footer{top:4600px;height:420px;background:var(--dark);color:#cfcfcf;display:flex;gap:50px;padding:44px 80px 0}
.footer h4{color:var(--orange);font-size:16px;font-weight:700;margin-bottom:18px}
.footer ul{list-style:none;font-size:13px;line-height:2}
.col-links{width:190px}.col-contact{width:260px}.col-news{width:300px}.col-social{width:180px}
.col-contact li{display:flex;align-items:center;gap:10px}
.footer p{font-size:13px;line-height:1.6}
.news-input{margin-top:16px;height:38px;background:#fff;border-radius:3px;width:280px}
.news-btn{margin-top:10px;display:inline-block;background:var(--orange);color:#fff;font-size:13px;font-weight:700;padding:8px 18px;border-radius:3px}
.col-social li{display:flex;align-items:center;gap:12px;margin-bottom:6px}
.social-dot{width:26px;height:26px;border-radius:4px;background:#44464b}
.copyright{position:absolute;top:5020px;left:0;width:1200px;height:48px;background:#141518;color:#888;font-size:12px;text-align:center;line-height:48px}
</style>
</head>
<body>

<header class="hero">
  <div class="placeholder hero-photo" role="img" aria-label="Technician repairing a smartphone at a workbench with tools"></div>
  <div class="hero-shade"></div>
  <nav class="nav">
    <div class="brand"><span class="brand-dot"></span>Handset Haven</div>
    <ul class="menu">
      <li>Process</li><li>Why choose us</li><li>Services</li><li>Team</li><li>Contacts</li><li>Testimonials</li><li>Key Performance</li><li>For Business</li>
    </ul>
    <a class="btn" href="#contact">Request a Repair</a>
  </nav>
  <div class="hero-copy">
    <h1>Best Mobile Repair Service <strong>At Any Time In Anywhere</strong></h1>
    <p>We are starting a new service that offers mobile device repairs on location, be it at the home of our customers, their office, or any other place. Just give us the address and we will come to you for the repair job.</p>
    <a class="btn" href="#contact">Request a Repair</a>
  </div>
</header>

<section class="process">
  <h2 class="section-title"><span class="light">Our</span><span class="bold">Process</span></h2>
  <div class="steps">
    <div class="step"><div class="step-art" role="img" aria-label="Character choosing a device on a phone"></div><h3>Choose your device and repair job</h3><p>Pick your model and the part that needs a fix in a few quick clicks.</p></div>
    <div class="step"><div class="step-art" role="img" aria-label="Character placing an order"></div><h3>Place the order</h3><p>Confirm your request online with clear pricing and no hidden cost.</p></div>
    <div class="step"><div class="step-art" role="img" aria-label="Character answering a callback"></div><h3>Get a callback within the hour</h3><p>Our call center phones you back for a short and friendly intake.</p></div>
    <div class="step"><div class="step-art" role="img" aria-label="Character holding a date and location sign"></div><h3>Set date and location</h3><p>Tell us where and when, home, office or any place you like.</p></div>
    <div class="step"><div class="step-art" role="img" aria-label="Engineer character arriving to help"></div><h3>We will come to you</h3><p>An engineer arrives and repairs your phone on the spot.</p></div>
  </div>
</section>

<section class="why">
  <h2 class="section-title"><span class="light">Why</span><span class="bold">Choose Us</span></h2>
  <div class="usps">
    <div class="usp"><div class="usp-ring"><div class="usp-core"><svg width="40" height="40" viewBox="0 0 40 40" fill="none" stroke="#fff" stroke-width="3"><circle cx="20" cy="13" r="7"/><path d="M6 36c2-9 8-12 14-12s12 3 14 12"/></svg></div></div><h3>Professional service on location</h3><p>Don't ship to us, we will come to you.</p></div>
    <div class="usp"><div class="usp-ring"><div class="usp-core"><svg width="40" height="40" viewBox="0 0 40 40" fill="none" stroke="#fff" stroke-width="3"><path d="M6 20 20 6h14v14L20 34z"/><circle cx="27" cy="13" r="2.5"/></svg></div></div><h3>Clear pricing upfront</h3><p>No hidden cost, ever.</p></div>
    <div class="usp"><div class="usp-ring"><div class="usp-core"><svg width="40" height="40" viewBox="0 0 40 40" fill="none" stroke="#fff" stroke-width="3"><path d="M13 6c-4 2-6 6-4 12s8 14 14 16 8 0 10-4l-6-5-4 3c-3-1-7-6-8-9l3-4z"/></svg></div></div><h3>Backed by a professional call center</h3><p>Open 12 hours a day and on Saturday too.</p></div>
    <div class="usp"><div class="usp-ring"><div class="usp-core"><svg width="40" height="40" viewBox="0 0 40 40" fill="none" stroke="#fff" stroke-width="3"><rect x="6" y="9" width="28" height="25" rx="2"/><path d="M6 16h28M13 5v7M27 5v7"/></svg></div></div><h3>Next business day</h3><p>Repair done the very next working day.</p></div>
    <div class="usp"><div class="usp-ring"><div class="usp-core"><svg width="40" height="40" viewBox="0 0 40 40" fill="none" stroke="#fff" stroke-width="3"><path d="M8 32 22 18M24 8a7 7 0 0 0 8 9l-4 4-6-6zM30 30 18 18M8 8l6 6"/></svg></div></div><h3>Backed by a professional repair center</h3><p>More than 12 years of experience.</p></div>
    <div class="usp"><div class="usp-ring"><div class="usp-core"><svg width="40" height="40" viewBox="0 0 40 40" fill="none" stroke="#fff" stroke-width="3"><circle cx="14" cy="14" r="5"/><circle cx="27" cy="14" r="5"/><path d="M4 32c1-6 5-9 10-9s9 3 10 9M20 27c1-3 4-4 7-4 5 0 8 3 9 9"/></svg></div></div><h3>Repair is done by certified engineers</h3><p>Skilled hands you can trust.</p></div>
    <div class="usp"><div class="usp-ring"><div class="usp-core"><svg width="40" height="40" viewBox="0 0 40 40" fill="none" stroke="#fff" stroke-width="3"><path d="M20 4 32 9v10c0 8-5 13-12 17C13 32 8 27 8 19V9z"/><path d="m14 20 5 5 8-9"/></svg></div></div><h3>1 year warranty</h3><p>On every repair we carry out.</p></div>
  </div>
</section>

<section class="services">
  <h2 class="section-title"><span class="light">What</span><span class="bold">We Do</span></h2>
  <div class="cards">
    <svg class="arrow left" viewBox="0 0 20 40"><path d="M16 4 4 20l12 16" fill="none" stroke="#999" stroke-width="3"/></svg>
    <article class="card"><div class="card-photo placeholder" role="img" aria-label="Smartphone with a cracked screen" style="background:linear-gradient(135deg,#8d7a66,#3e3a36)"></div><h3>Broken Screens</h3><p>Cracked or shattered display? We replace the glass and screen while you wait.</p></article>
    <article class="card"><div class="card-photo placeholder" role="img" aria-label="Phone battery being replaced" style="background:linear-gradient(135deg,#c9ccd0,#7c8289)"></div><h3>Broken Batteries</h3><p>Phone dies too fast? A fresh battery gets you through the whole day again.</p></article>
    <article class="card"><div class="card-photo placeholder" role="img" aria-label="Phone dropped in water" style="background:linear-gradient(135deg,#7fb6d6,#2d6f99)"></div><h3>Water Damage</h3><p>Dropped in water? We dry, clean and restore the inner parts on location.</p></article>
    <article class="card"><div class="card-photo placeholder" role="img" aria-label="Close-up of a phone camera lens" style="background:linear-gradient(135deg,#b9b3ad,#56514c)"></div><h3>Broken Camera's</h3><p>Blurry photos or a dead lens? We fit a new camera module in no time.</p></article>
    <svg class="arrow right" viewBox="0 0 20 40"><path d="M4 4 16 20 4 36" fill="none" stroke="#999" stroke-width="3"/></svg>
  </div>
</section>

<section class="team">
  <div class="team-head">
    <div><h2>MEET THE TEAM</h2><div class="sub">We have <b>*10 years</b> Experience</div></div>
    <p>We have multiple skilled engineers who drive trough the country on a daily basis and can be on location within a working day. Repair is done immediately onsite while the customer waits. Your phone is being repaired directly in front of you, the next business day, on a location you desire.</p>
  </div>
  <div class="members">
    <div class="member"><div class="member-photo placeholder" role="img" aria-label="Portrait of engineer" style="background:linear-gradient(180deg,#c5c7ca,#7a7e84)"></div><h4>DAAN VISSER</h4><span>SENIOR TECHNICIAN</span></div>
    <div class="member"><div class="member-photo placeholder" role="img" aria-label="Portrait of engineer" style="background:linear-gradient(180deg,#d2cdc8,#8a837d)"></div><h4>SANNE DE VRIES</h4><span>SENIOR TECHNICIAN</span></div>
    <div class="member"><div class="member-photo placeholder" role="img" aria-label="Portrait of engineer" style="background:linear-gradient(180deg,#c8c8c8,#6f6f6f)"></div><h4>BRAM JANSEN</h4><span>SENIOR TECHNICIAN</span></div>
    <div class="member"><div class="member-photo placeholder" role="img" aria-label="Portrait of engineer" style="background:linear-gradient(180deg,#cfd2d4,#80868b)"></div><h4>LUCAS BAKKER</h4><span>SENIOR TECHNICIAN</span></div>
    <div class="member"><div class="member-photo placeholder" role="img" aria-label="Portrait of engineer" style="background:linear-gradient(180deg,#d4cfca,#7d766f)"></div><h4>MILAN SMIT</h4><span>SENIOR TECHNICIAN</span></div>
  </div>
</section>

<section class="contact" id="contact">
  <div class="placeholder contact-photo" role="img" aria-label="Photo of a hand holding out a company business card"></div>
  <div class="contact-form">
    <h2>Contact Us <b>For Any Questions</b></h2>
    <div class="field">* First Name</div>
    <div class="field">* Last Name</div>
    <div class="field">* Email Address</div>
    <div class="field">* Phone Number</div>
    <a class="btn" href="#contact">Request a Repair</a>
  </div>
</section>

<section class="testimonials">
  <h2 class="section-title"><span class="light">Client</span><span class="bold">Testimonials</span></h2>
  <div class="quotes">
    <div class="quote"><div class="quote-avatar" role="img" aria-label="Customer portrait"></div><div class="quote-mark">&ldquo;</div><div><p>They came to my office the next morning and fixed my cracked screen while I had coffee. Fast, friendly and no surprises on the bill.</p><cite>- Eva Mulder</cite></div></div>
    <div class="quote"><div class="quote-avatar" role="img" aria-label="Customer portrait"></div><div class="quote-mark">&ldquo;</div><div><p>My phone took a swim and I thought it was gone. The engineer brought it back to life right at my front door.</p><cite>- Tom de Boer</cite></div></div>
  </div>
</section>

<section class="kpi">
  <div class="placeholder kpi-photo" role="img" aria-label="Smiling person using a smartphone"></div>
  <h2 class="section-title"><span class="light">Key</span><span class="bold">Performance</span></h2>
  <div class="kpi-list">
    <div class="kpi-item"><div class="kpi-icon"><svg width="56" height="56" viewBox="0 0 40 40" fill="#fff"><circle cx="20" cy="12" r="6"/><circle cx="9" cy="15" r="4"/><circle cx="31" cy="15" r="4"/><path d="M8 34c0-8 5-12 12-12s12 4 12 12zM1 30c0-6 3-9 8-9 2 0 3 .5 4 1-3 2-5 5-5 8zM39 30c0-6-3-9-8-9-2 0-3 .5-4 1 3 2 5 5 5 8z"/></svg></div><h3>Experienced Team</h3><p>Certified engineers with years of hands-on repair work.</p></div>
    <div class="kpi-item"><div class="kpi-icon"><svg width="50" height="50" viewBox="0 0 40 40" fill="none" stroke="#fff" stroke-width="3"><rect x="11" y="3" width="18" height="34" rx="3"/><path d="M17 31h6"/></svg></div><h3>Original Gadgets</h3><p>Only genuine parts and quality tools in every van.</p></div>
    <div class="kpi-item"><div class="kpi-icon"><svg width="50" height="50" viewBox="0 0 40 40"><text x="20" y="33" text-anchor="middle" font-family="Raleway,sans-serif" font-weight="800" font-size="36" fill="#fff">$</text></svg></div><h3>Reasonable Price</h3><p>Clear pricing upfront with no hidden cost.</p></div>
    <div class="kpi-item"><div class="kpi-icon"><svg width="56" height="56" viewBox="0 0 40 40" fill="none" stroke="#fff" stroke-width="3"><circle cx="20" cy="20" r="16"/><circle cx="14" cy="16" r="1.5" fill="#fff"/><circle cx="26" cy="16" r="1.5" fill="#fff"/><path d="M12 24c4 5 12 5 16 0"/></svg></div><h3>Customer Satisfaction</h3><p>Happy customers who are connected again.</p></div>
  </div>
</section>

<section class="business">
  <h2>For <b>Businees</b></h2>
  <div class="biz-copy">
    <h3>The services we provide for corporate clients are-</h3>
    <ul>
      <li>On-site repairs at your office</li>
      <li>Fleet service contracts for company phones</li>
      <li>Priority support with a dedicated contact</li>
    </ul>
  </div>
</section>

<footer class="footer">
  <div class="col-links"><h4>Quick Links</h4><ul><li>Home</li><li>Who We Are</li><li>What We Do</li><li>Our Process</li><li>Pricing</li><li>Testimonials</li><li>Our Clients</li><li>Contact Us</li></ul></div>
  <div class="col-contact"><h4>Contact Information</h4><ul>
    <li><svg width="14" height="18" viewBox="0 0 14 18"><path d="M7 1a6 6 0 0 0-6 6c0 5 6 10 6 10s6-5 6-10a6 6 0 0 0-6-6z" fill="var(--orange)"/><circle cx="7" cy="7" r="2" fill="#1e1f22"/></svg>12 Havenstraat, Rotterdam</li>
    <li><svg width="14" height="18" viewBox="0 0 14 18"><rect x="2" y="1" width="10" height="16" rx="2" fill="var(--orange)"/></svg>010-555-0142</li>
    <li><svg width="16" height="12" viewBox="0 0 16 12"><rect width="16" height="12" rx="1" fill="var(--orange)"/><path d="M1 1l7 6 7-6" fill="none" stroke="#1e1f22" stroke-width="1.5"/></svg>contact@handsethaven.com</li>
  </ul></div>
  <div class="col-news"><h4>Newsletter Signup</h4><p>Please enter your email address below to receive our free newsletter.</p><div class="news-input"></div><span class="news-btn">Subscribe</span></div>
  <div class="col-social"><h4>Follow Us</h4><ul>
    <li><span class="social-dot"></span>Facefolio</li>
    <li><span class="social-dot"></span>Linkwork</li>
    <li><span class="social-dot"></span>Chirper</li>
    <li><span class="social-dot"></span>Email</li>
  </ul></div>
</footer>
<div class="copyright">Copyright &copy; Handset Haven. All Rights Reserved.</div>

</body>
</html>
```